GivingGavelHub Website Redesign

I'm looking to give our website a new look and feel with better graphics/images and that is focused on conversions.
www.givinggavelhub.example. The content can stay the same. Im looking for a new hero section with maybe a call to auction form to create an auction by asking for the following information: Event Name, Event Benefits, Country, Time zone and currency.
Our goal is to show that we can host online auctions, mobile auctions and live in-person auction. The content does not need to change on the site. We just need sections or illustrations that represent those features. It would also be good to have a sections that will segment our users into the following categories: Nonprofits/Charities, Schools/Education, Businesses, Government Agency, Individual.
The following pages need to be updated:
https://www.givinggavelhub.example/
https://www.givinggavelhub.example/online-bidding-features
https://www.givinggavelhub.example/online-bidding-experience
https://www.givinggavelhub.example/about
https://www.givinggavelhub.example/pricing
Updates
This project would cover the following 4 pages:
https://www.givinggavelhub.example

```html
<!DOCTYPE html>
<html lang="en">
<head>
<meta charset="utf-8">
<title>GivingGavelHub — Homepage</title>
<link href="https://fonts.googleapis.com/css2?family=Outfit:wght@400;500;600;700&family=Montserrat:wght@400;500;600;700&family=Lora:wght@400&display=swap" rel="stylesheet">
<style>
:root{
  --sky:#4499f6;
  --hero:#0b56b3;
  --navy:#0f2a5c;
  --ink:#1a2238;
  --muted:#5d667a;
  --blue:#3a8ef0;
  --blue-light:#4ea6ff;
  --orange:#f0573a;
  --orange-dark:#da4a30;
  --card:#d6e3f1;
  --soft:#eef3f9;
  --soft2:#d9e5f2;
  --page:#f3f6fa;
  --footer:#0b2445;
  --green:#2fb89a;
  --line:#e2e8f0;
}
*{box-sizing:border-box;margin:0;padding:0}
html,body{width:944px;height:1200px;overflow:hidden;background:var(--sky)}
body{font-family:"Montserrat",sans-serif;color:var(--ink)}
.stage{position:absolute;left:0;top:0;width:1708px;height:2172px;transform:scale(0.552693);transform-origin:0 0;background:var(--sky);overflow:hidden}
.abs{position:absolute}
.panel{position:absolute;overflow:hidden}
.center{text-align:center}
.h-display{font-family:"Outfit",sans-serif;font-weight:600;letter-spacing:-0.2px}
.accent{color:var(--blue)}
.btn{position:absolute;display:flex;align-items:center;justify-content:center;font-family:"Montserrat",sans-serif;font-weight:600;font-size:7.5px;letter-spacing:.3px;color:#fff;text-transform:uppercase;border-radius:2px}
.btn-orange{background:var(--orange);box-shadow:0 4px 10px rgba(240,87,58,.3)}
.btn-blue{background:var(--blue);box-shadow:0 4px 10px rgba(58,142,240,.3)}
.art{position:absolute}

/* scene fills that blend into their section */
.scene-hero{background:radial-gradient(ellipse at 50% 80%,rgba(47,184,154,.55),rgba(58,142,240,.35) 55%,rgba(11,86,179,0) 75%)}
.scene-warm{background:radial-gradient(ellipse at 50% 60%,rgba(58,142,240,.75),rgba(47,184,154,.45) 50%,rgba(240,87,58,0) 75%)}
.scene-card{background:radial-gradient(ellipse at 50% 55%,rgba(47,184,154,.55),rgba(58,142,240,.4) 50%,rgba(255,255,255,0) 72%)}

/* left page */
.page-left{left:14px;top:85px;width:834px;height:2087px;background:var(--page)}
.nav{left:0;top:0;width:834px;height:43px;background:#fff}
.brand{position:absolute;display:flex;align-items:center;gap:6px;font-family:"Outfit",sans-serif;font-weight:500;font-size:15px;color:var(--blue)}
.brand-dot{width:18px;height:18px;border-radius:50%;background:var(--blue)}
.nav-link{position:absolute;top:18px;font-size:7px;color:var(--ink)}
.nav-circle{position:absolute;top:11px;width:21px;height:21px;border-radius:50%}
.hero{left:0;top:43px;width:834px;height:425px;background:var(--hero);color:#fff}
.hero h1{position:absolute;left:0;top:62px;width:834px;font-size:27px;line-height:27px;color:#fff}
.hero h1 .accent{color:var(--blue-light)}
.hero-lead{position:absolute;left:167px;top:123px;width:500px;font-size:9.3px;line-height:15px;color:#e3ecf9}
.field-label{position:absolute;font-size:6.5px;font-weight:600;color:#fff;letter-spacing:.2px}
.field{position:absolute;height:30px;border:1px solid rgba(255,255,255,.35);border-radius:2px;font-size:6.5px;color:rgba(255,255,255,.55);padding:11px 0 0 14px}
.hero-note{position:absolute;left:0;top:322px;width:834px;font-size:6.5px;color:#cfe0f6}
.cloud{position:absolute;height:14px;border-radius:10px;background:#a9d1fb}

.spend{left:0;top:468px;width:834px;height:580px;background:var(--soft)}
.section-title{position:absolute;left:0;width:100%;font-size:30px;line-height:28px;color:var(--navy)}
.benefit{position:absolute;top:131px;width:245px;height:284px;background:var(--card);border-radius:10px}
.benefit h3{position:absolute;left:0;top:98px;width:100%;font-family:"Outfit",sans-serif;font-weight:600;font-size:13.5px;line-height:16px;color:var(--ink)}
.benefit p{position:absolute;left:22px;top:138px;width:201px;font-size:7.3px;line-height:10.5px;color:var(--muted)}
.testimonial{position:absolute;top:370px;width:218px;height:117px;background:#fff;border-radius:4px}
.testimonial blockquote{position:absolute;left:12px;top:24px;width:194px;font-family:"Lora",serif;font-size:7.5px;line-height:11px;color:#333;text-align:center}
.quote-mark{position:absolute;left:8px;top:74px;font-family:"Lora",serif;font-size:54px;color:#dde2ea;line-height:54px}
.avatar{position:absolute;top:95px;width:38px;height:38px;border-radius:50%;background:linear-gradient(135deg,#c9a58c,#7b8aa8);border:2px solid #fff}
.reviewer{position:absolute;top:512px;width:245px;font-size:6.5px;font-weight:700;color:var(--navy);text-transform:uppercase}
.reviewer span{color:var(--blue)}
.stars{position:absolute;top:522px;width:245px;font-size:13px;color:#f5a623;letter-spacing:1px}

.build{left:0;top:1048px;width:834px;height:469px;background:var(--soft2)}
.step{position:absolute;top:132px;width:201px;height:253px;background:#fff;border-radius:8px;overflow:hidden}
.step h3{position:absolute;left:0;top:128px;width:100%;font-family:"Outfit",sans-serif;font-weight:600;font-size:22px;color:var(--ink)}
.step p{position:absolute;left:18px;top:160px;width:165px;font-size:7.8px;line-height:11.5px;color:var(--muted)}
.step-num{position:absolute;left:0;top:206px;width:100%;font-family:"Outfit",sans-serif;font-weight:700;font-size:62px;color:#e4ebf4}
.step-arrow{position:absolute;top:252px;width:12px;height:12px}

.support{left:0;top:1517px;width:834px;height:303px;background:var(--orange)}
.support-strip{position:absolute;left:0;top:0;width:834px;height:20px;background:var(--orange-dark)}
.support h2{position:absolute;left:417px;top:82px;font-size:32px;line-height:31px;color:#fff}
.support p{position:absolute;left:417px;top:186px;width:290px;font-size:9.8px;line-height:17px;color:#fff}
.btn-white{background:#fff;color:var(--orange);font-weight:500}

.features{left:0;top:1820px;width:834px;height:267px;background:var(--page)}
.feature{position:absolute;width:202px;background:var(--card);border-radius:8px}
.feature.active{background:#fff;box-shadow:0 6px 18px rgba(20,40,80,.12)}
.feature h3{position:absolute;left:0;top:49px;width:100%;font-family:"Outfit",sans-serif;font-weight:600;font-size:13px;color:var(--ink)}
.feature p{position:absolute;left:24px;top:71px;width:154px;font-size:6.9px;line-height:10.4px;color:var(--muted)}
.feature-icon{position:absolute;width:62px;height:62px;border-radius:50%;background:#fff;box-shadow:0 4px 12px rgba(20,40,80,.1);display:flex;align-items:center;justify-content:center}
.feature-icon.filled{background:var(--green)}

/* right page */
.page-right{left:862px;top:0;width:833px;height:2150px;background:var(--page)}
.top-features{left:0;top:0;width:833px;height:460px;background:var(--soft)}
.faq{left:0;top:460px;width:833px;height:528px;background:var(--hero);color:#fff}
.faq h2{position:absolute;left:0;top:45px;width:100%;font-size:31px;color:#fff}
.faq h2 .accent{color:var(--blue-light)}
.faq-sub{position:absolute;left:0;top:88px;width:100%;font-size:10.5px;line-height:15px;font-weight:500;color:#fff}
.faq-list{position:absolute;top:134px;width:290px;list-style:none}
.faq-list li{height:44px;border-bottom:1px solid rgba(255,255,255,.25);display:flex;align-items:center;justify-content:space-between;font-size:7.3px;font-weight:500;color:#fff}
.faq-list li b{color:var(--orange);font-size:12px;font-weight:600;margin-right:8px}

.download{left:0;top:988px;width:833px;height:292px;background:var(--page)}
.download h2{position:absolute;left:443px;top:65px;font-size:27px;line-height:31px;color:#0d52a8}
.download p{position:absolute;left:443px;top:142px;width:300px;font-size:10px;line-height:16.5px;color:#333}
.divider{position:absolute;left:98px;bottom:0;width:637px;height:1px;background:var(--line)}

.blog{left:0;top:1280px;width:833px;height:635px;background:var(--page)}
.post{position:absolute;top:113px;width:201px;height:257px;background:#fff;border:1px solid var(--line);border-radius:4px}
.post-image{position:absolute;left:4px;top:4px;width:191px;height:128px;border-radius:2px;display:flex;align-items:center;justify-content:center}
.post-image span{display:block;width:150px;padding:10px 6px;background:rgba(255,255,255,.8);font-family:"Outfit",sans-serif;font-size:10.5px;line-height:14px;color:#1b1b1b;text-align:center;text-transform:uppercase;font-weight:500}
.post p{position:absolute;left:10px;top:150px;width:179px;font-size:11px;line-height:15px;color:#222;text-align:center}
.company{position:absolute;left:96px;top:420px;width:639px;height:147px;background:var(--blue);border-radius:8px}
.company-wrap{position:absolute;left:0;top:0;width:833px;height:635px}
.company h2{position:absolute;left:0;top:32px;width:100%;font-size:31px;color:#fff}
.company-sub{position:absolute;left:0;top:74px;width:100%;font-size:8px;color:#e6f0fd}
.partner{position:absolute;top:530px;width:114px;height:59px;background:#fff;border-radius:3px;box-shadow:0 4px 10px rgba(20,40,80,.1);display:flex;align-items:center;justify-content:center}
.partner i{display:block;width:34px;height:34px;border-radius:6px;background:#cfd6e2}

.footer{left:0;top:1915px;width:833px;height:235px;background:var(--footer);color:#fff}
.footer-rule{position:absolute;top:0;width:1px;height:190px;background:rgba(255,255,255,.12)}
.footer h4{position:absolute;font-size:7.5px;font-weight:700;letter-spacing:.4px}
.footer-links{position:absolute;list-style:none;font-size:7.5px;line-height:15.6px;color:#d7e1ef}
.social{position:absolute;top:112px;width:22px;height:22px;border-radius:50%;background:var(--blue)}
.copyright{position:absolute;left:0;top:190px;width:100%;font-size:6.5px;color:#c6d1e0;text-align:center;border-top:1px solid rgba(255,255,255,.12);padding-top:20px}
</style>
</head>
<body>
<div class="stage">

<main class="panel page-left">

  <header class="panel nav">
    <div class="brand" style="left:26px;top:12px"><span class="brand-dot"></span>GivingGavelHub</div>
    <span class="nav-link" style="left:284px">How It Works</span>
    <span class="nav-link" style="left:355px">Pricing</span>
    <span class="nav-link" style="left:406px">About</span>
    <span class="nav-link" style="left:455px">Blog</span>
    <span class="nav-circle" style="left:548px;background:var(--blue)">
      <svg width="21" height="21" viewBox="0 0 21 21"><circle cx="9.5" cy="9.5" r="4" fill="none" stroke="#fff" stroke-width="1.5"/><path d="M12.5 12.5l3.5 3.5" stroke="#fff" stroke-width="1.5"/></svg>
    </span>
    <span class="nav-circle" style="left:578px;background:#e9eef6">
      <svg width="21" height="21" viewBox="0 0 21 21"><circle cx="10.5" cy="8" r="3" fill="none" stroke="var(--blue)" stroke-width="1.2"/><path d="M5 16c1-3 3-4 5.5-4s4.5 1 5.5 4" fill="none" stroke="var(--blue)" stroke-width="1.2"/></svg>
    </span>
    <span class="nav-link" style="left:605px;font-weight:600">SIGN IN ⌄</span>
    <span class="btn" style="left:650px;top:11px;width:58px;height:22px;border:1px solid var(--blue);color:var(--blue);font-size:6.5px">For Bidders</span>
    <span class="btn btn-orange" style="left:724px;top:11px;width:84px;height:22px;font-size:6.5px">For Fundraiser</span>
  </header>

  <section class="panel hero">
    <span class="cloud" style="left:108px;top:50px;width:40px"></span>
    <span class="cloud" style="left:40px;top:85px;width:50px;height:18px"></span>
    <span class="cloud" style="left:716px;top:138px;width:40px"></span>
    <span class="cloud" style="left:773px;top:174px;width:50px;height:18px"></span>

    <div class="art scene-hero" role="img" aria-label="Illustration of people setting up an online auction on a large screen" style="left:10px;top:275px;width:235px;height:150px"></div>
    <div class="art scene-hero" role="img" aria-label="Illustration of auction items being built with cranes and shopping carts" style="left:270px;top:340px;width:295px;height:85px"></div>
    <div class="art scene-hero" role="img" aria-label="Illustration of a mobile phone building with people bidding" style="left:580px;top:270px;width:245px;height:155px"></div>

    <h1 class="h-display center">You've Just Found The <span class="accent">Easiest Online</span><br><span class="accent">Auction Platform</span> To Use, Period.</h1>
    <p class="hero-lead center">GivingGavelHub has eliminated the headache of setting up online and in-person auctions. We've simplified everything to get you up and running quickly without the help of a tech team.</p>

    <form>
      <span class="field-label" style="left:204px;top:174px">NAME YOUR EVENT*</span>
      <div class="field" style="left:190px;top:179px;width:226px">Event Name...</div>
      <span class="field-label" style="left:436px;top:174px">EVENT BENEFITS*</span>
      <div class="field" style="left:422px;top:179px;width:227px">Organization Name...</div>
      <span class="field-label" style="left:204px;top:222px">COUNTRY*</span>
      <div class="field" style="left:190px;top:227px;width:148px">United States</div>
      <span class="field-label" style="left:359px;top:222px">TIME ZONE*</span>
      <div class="field" style="left:344px;top:227px;width:149px">Eastern Standard Time...</div>
      <span class="field-label" style="left:514px;top:222px">CURRENCY*</span>
      <div class="field" style="left:500px;top:227px;width:149px">Dollar | $</div>
      <span class="btn btn-orange" style="left:356px;top:284px;width:122px;height:33px">Build An Auction</span>
    </form>
    <p class="hero-note center">*No credit card required</p>
  </section>

  <section class="panel spend">
    <h2 class="section-title h-display center" style="top:55px">Spend less time.<br>Make more <span class="accent">money.</span></h2>

    <article class="benefit" style="left:26px">
      <div class="art scene-card" role="img" aria-label="Illustration of a laptop showing an auction dashboard" style="left:72px;top:18px;width:100px;height:66px"></div>
      <h3 class="center">Quickly create, design and<br>manage auctions.</h3>
      <p class="center">You are only 5 minutes away from having your auction built and ready for items. We took the pain and confusion out of getting started.</p>
      <span class="btn btn-orange" style="left:65px;top:193px;width:115px;height:24px">Build An Auction</span>
    </article>
    <article class="benefit" style="left:295px">
      <div class="art scene-card" role="img" aria-label="Illustration of a hand holding a phone with auction items" style="left:72px;top:18px;width:100px;height:66px"></div>
      <h3 class="center">More money goes directly<br>to your cause.</h3>
      <p class="center">You can accept cash, checks, bank transfers, or credit cards. It's your money, collect it on your own terms.</p>
      <span class="btn btn-orange" style="left:65px;top:193px;width:115px;height:24px">Collect More Money</span>
    </article>
    <article class="benefit" style="left:564px">
      <div class="art scene-card" role="img" aria-label="Illustration of people managing donors on screens" style="left:72px;top:18px;width:100px;height:66px"></div>
      <h3 class="center">Manage your donors and<br>donations effortlessly.</h3>
      <p class="center">Our Donation CRM allows you to easily track all donations and donors in an easy-to-use dashboard. Export all information or sync with our integration partners to unlock more donor management tools.</p>
      <span class="btn btn-orange" style="left:65px;top:193px;width:115px;height:24px">Manage My Donars</span>
    </article>

    <figure class="testimonial" style="left:40px">
      <blockquote>"I'm 74 years old and I didn't need to call my Grandkids to set up this auction for me! The software was easy to use and the end of auction experience was a breeze!"</blockquote>
      <span class="quote-mark">“</span>
      <span class="avatar" role="img" aria-label="Portrait photo of the reviewer" style="left:90px"></span>
    </figure>
    <figure class="testimonial" style="left:308px">
      <blockquote>"We just completed an auction that raised over $30,000 for a family battling cancer. GivingGavelHub made it possible with very little cost. 100% we will use them again."</blockquote>
      <span class="quote-mark">“</span>
      <span class="avatar" role="img" aria-label="Portrait photo of the reviewer" style="left:90px"></span>
    </figure>
    <figure class="testimonial" style="left:577px">
      <blockquote>GGH-auction-testim4"The people coming to our events say it's easy to use and we can check people out so much faster than we ever could in the past. I highly recommend trying GivingGavelHub out, you'll never go anywhere else."</blockquote>
      <span class="quote-mark">“</span>
      <span class="avatar" role="img" aria-label="Portrait photo of the reviewer" style="left:90px"></span>
    </figure>

    <p class="reviewer center" style="left:26px">Marlene B. - <span>Lakeside Service Club</span></p>
    <p class="stars center" style="left:26px">★★★★★</p>
    <p class="reviewer center" style="left:295px">Daniel Whitford - <span>Harlow Family Fund</span></p>
    <p class="stars center" style="left:295px">★★★★★</p>
    <p class="reviewer center" style="left:564px">Owen Kessler - <span>North Ridge Rovers</span></p>
    <p class="stars center" style="left:564px">★★★★★</p>
  </section>

  <section class="panel build">
    <h2 class="section-title h-display center" style="top:45px">Build your <span class="accent">auction</span><br><span class="accent">in minutes,</span> not days.</h2>

    <article class="step" style="left:98px">
      <div class="art scene-card" role="img" aria-label="Illustration of a person building an auction page with a crane" style="left:26px;top:14px;width:150px;height:112px"></div>
      <h3 class="center">Build</h3>
      <p class="center">Answer a few questions about your event and your auction will be ready to populate with items in less than 5 minutes.</p>
      <span class="step-num center">01</span>
    </article>
    <svg class="step-arrow" style="left:294px" viewBox="0 0 12 12"><path d="M2 2l4 4-4 4M6 2l4 4-4 4" fill="none" stroke="#555" stroke-width="1"/></svg>
    <article class="step" style="left:316px">
      <div class="art scene-card" role="img" aria-label="Illustration of auction items loaded into a cart" style="left:26px;top:14px;width:150px;height:112px"></div>
      <h3 class="center">Add</h3>
      <p class="center">Upload items in bulk or add them one at a time. Our item wizard will walk you through the process.</p>
      <span class="step-num center">02</span>
    </article>
    <svg class="step-arrow" style="left:513px" viewBox="0 0 12 12"><path d="M2 2l4 4-4 4M6 2l4 4-4 4" fill="none" stroke="#555" stroke-width="1"/></svg>
    <article class="step" style="left:534px">
      <div class="art scene-card" role="img" aria-label="Illustration of people sharing an auction from their phones" style="left:26px;top:14px;width:150px;height:112px"></div>
      <h3 class="center">Share</h3>
      <p class="center">When you are ready to go live, share your auction's custom URL through email, social media, and your website.</p>
      <span class="step-num center">03</span>
    </article>

    <span class="btn btn-orange" style="left:326px;top:409px;width:182px;height:31px">I'm Ready To Build My Auction</span>
  </section>

  <section class="panel support">
    <div class="support-strip"></div>
    <span class="cloud" style="left:108px;top:100px;width:48px;height:20px"></span>
    <span class="cloud" style="left:175px;top:73px;width:40px"></span>
    <div class="art scene-warm" role="img" aria-label="Illustration of support staff helping people on a large screen with headset icon" style="left:110px;top:120px;width:250px;height:183px"></div>
    <h2 class="h-display">Friendly technical<br>support and training<br>when you need it.</h2>
    <p>Other companies charge hundreds of dollars for your auction support and training. We offer it for free.</p>
    <span class="btn btn-white" style="left:417px;top:234px;width:106px;height:26px">Schedule A Call</span>
  </section>

  <section class="panel features">
    <h2 class="section-title h-display center" style="top:55px;font-size:31px;line-height:31px">Every Charity Auction comes<br>packed with all the features you<br>need to run a <span class="accent">live event too.</span></h2>

    <article class="feature" style="left:98px;top:200px;height:100px">
      <h3 class="center">Pre-Register Guests</h3>
    </article>
    <article class="feature active" style="left:316px;top:200px;height:100px">
      <h3 class="center">Attendee Management</h3>
    </article>
    <article class="feature" style="left:534px;top:200px;height:100px">
      <h3 class="center">Accept Donations</h3>
    </article>
    <span class="feature-icon" style="left:168px;top:169px">
      <svg width="28" height="28" viewBox="0 0 28 28"><rect x="5" y="4" width="16" height="20" rx="2" fill="none" stroke="var(--green)" stroke-width="2"/><path d="M9 10h8M9 14h8M9 18h5" stroke="var(--green)" stroke-width="2"/></svg>
    </span>
    <span class="feature-icon filled" style="left:386px;top:169px">
      <svg width="28" height="28" viewBox="0 0 28 28"><circle cx="10" cy="10" r="4" fill="#fff"/><circle cx="19" cy="10" r="4" fill="#fff"/><path d="M3 23c1-5 4-7 7-7s6 2 7 7M12 23c1-5 4-7 7-7s6 2 7 7" fill="#fff"/></svg>
    </span>
    <span class="feature-icon" style="left:604px;top:169px">
      <svg width="28" height="28" viewBox="0 0 28 28"><circle cx="17" cy="9" r="5" fill="var(--green)"/><path d="M3 20l6-3h8l-2 3h6l4-4" fill="none" stroke="var(--green)" stroke-width="2"/></svg>
    </span>
  </section>
</main>

<main class="panel page-right">

  <section class="panel top-features">
    <article class="feature" style="left:96px;top:4px;height:141px">
      <h3 class="center">Pre-Register Guests</h3>
      <p class="center">When you pre-register your guests, this gets everyone set up for the auction before it begins. Pre-register guests and let them start bidding as soon as they get a ticket.</p>
    </article>
    <article class="feature active" style="left:315px;top:4px;height:141px">
      <h3 class="center">Attendee Management</h3>
      <p class="center">Manage your attendee communications via your GivingGavelHub dashboard. Our donor management system works for you so you can raise more funds, and help more people.</p>
    </article>
    <article class="feature" style="left:533px;top:4px;height:141px">
      <h3 class="center">Accept Donations</h3>
      <p class="center">We have integrated payment systems so you can accept donations via credit card, check, e-wallet, and more.</p>
    </article>
    <span class="feature-icon" style="left:166px;top:-29px"></span>
    <span class="feature-icon filled" style="left:385px;top:-29px"></span>
    <span class="feature-icon" style="left:603px;top:-29px"></span>

    <article class="feature" style="left:96px;top:195px;height:141px">
      <h3 class="center">Pre-Register Guests</h3>
      <p class="center">When you pre-register your guests, this gets everyone set up for the auction before it begins. Pre-register guests and let them start bidding as soon as they get a ticket.</p>
    </article>
    <article class="feature" style="left:315px;top:195px;height:141px">
      <h3 class="center">Attendee Management</h3>
      <p class="center">Manage your attendee communications via your GivingGavelHub dashboard. Our donor management system works for you so you can raise more funds, and help more people.</p>
    </article>
    <article class="feature" style="left:533px;top:195px;height:141px">
      <h3 class="center">Accept Donations</h3>
      <p class="center">We have integrated payment systems so you can accept donations via credit card, check, e-wallet, and more.</p>
    </article>
    <span class="feature-icon" style="left:166px;top:162px">
      <svg width="30" height="28" viewBox="0 0 30 28"><path d="M4 6h4l3 12h13l3-9H10" fill="none" stroke="var(--green)" stroke-width="2"/><circle cx="13" cy="22" r="2" fill="var(--green)"/><circle cx="22" cy="22" r="2" fill="var(--green)"/></svg>
    </span>
    <span class="feature-icon" style="left:385px;top:162px">
      <svg width="28" height="28" viewBox="0 0 28 28"><circle cx="17" cy="9" r="5" fill="var(--green)"/><path d="M3 20l6-3h8l-2 3h6l4-4" fill="none" stroke="var(--green)" stroke-width="2"/></svg>
    </span>
    <span class="feature-icon" style="left:603px;top:162px">
      <svg width="28" height="28" viewBox="0 0 28 28"><rect x="4" y="10" width="20" height="14" rx="1" fill="var(--green)"/><path d="M8 10l4-5 8 5" fill="none" stroke="var(--green)" stroke-width="2"/></svg>
    </span>

    <span class="btn btn-orange" style="left:248px;top:370px;width:165px;height:33px">I'm Ready To Get Started</span>
    <span class="btn btn-blue" style="left:420px;top:370px;width:167px;height:33px">Schedule A Consultation</span>
  </section>

  <section class="panel faq">
    <span class="cloud" style="left:34px;top:130px;width:40px;height:18px"></span>
    <span class="cloud" style="left:763px;top:68px;width:42px;height:18px"></span>
    <div class="art scene-hero" role="img" aria-label="Illustration of people building an auction with screens, cranes and a mobile building" style="left:20px;top:375px;width:790px;height:153px"></div>
    <h2 class="h-display center">Frequently <span class="accent">Asked</span> Questions</h2>
    <p class="faq-sub center">Don't worry, if you have some questions, you aren't alone.<br>Here are answers to some of the most common questions we get.</p>
    <ul class="faq-list" style="left:98px">
      <li>Can I Pass Fees Onto Bidders? <b>+</b></li>
      <li>Can I Download All My Bidder Data? <b>+</b></li>
      <li>Can You Mail Me A Check? <b>+</b></li>
      <li>How Much Are Credit Card Processing Fees? <b>+</b></li>
      <li>Can I Start My Auction Online And Bring It Offline? <b>+</b></li>
    </ul>
    <ul class="faq-list" style="left:446px">
      <li>What Happens If Items Don't Sell? <b>+</b></li>
      <li>What Is The Management Fee? <b>+</b></li>
      <li>How Do I Pay Our Management Fee And Receive My Funds? <b>+</b></li>
      <li>Can We Collect Cash Or Checks Offline For Items? <b>+</b></li>
      <li>What If I Have More Questions? <b>+</b></li>
    </ul>
  </section>

  <section class="panel download">
    <div class="art" role="img" aria-label="Laptop and tablet showing the Auction Growth Playbook guide cover" style="left:96px;top:25px;width:292px;height:235px;background:radial-gradient(ellipse at 55% 50%,#3d5f96,#8ea3c4 45%,rgba(243,246,250,0) 72%)"></div>
    <h2 class="h-display">Download the Auction<br>Growth PlaybookTM</h2>
    <p>Learn the 4 tools BIG Organizations use to skyrocket their auction profits! Stop leaving thousands of dollars on the table by <b>following this Step-By-Step Guide.</b></p>
    <span class="btn btn-orange" style="left:443px;top:206px;width:165px;height:33px">I'm Ready To Get Started</span>
    <div class="divider"></div>
  </section>

  <section class="panel blog">
    <h2 class="section-title h-display center" style="top:55px;line-height:34px">Latest Blog <span class="accent">Post.</span></h2>

    <article class="post" style="left:98px">
      <div class="post-image" role="img" aria-label="Photo of a desk workspace behind the post title" style="background:linear-gradient(135deg,#a58a6a,#5a4d40)"><span>The definitive guide to setting up an online auction</span></div>
      <p>Follow this Step-by-Step guide to learn how to easily create and manage your first auction.</p>
      <span class="btn btn-orange" style="left:56px;top:209px;width:88px;height:24px">Learn More</span>
    </article>
    <article class="post" style="left:316px">
      <div class="post-image" role="img" aria-label="Photo of a laptop surrounded by social media tiles behind the post title" style="background:linear-gradient(135deg,#b9a48d,#6e8fbf)"><span>4 top tips for using social media to boost your fundraiser</span></div>
      <p>Follow this Step-by-Step guide to learn how to easily create and manage your first auction.</p>
      <span class="btn btn-blue" style="left:56px;top:209px;width:88px;height:24px">Learn More</span>
    </article>
    <article class="post" style="left:534px">
      <div class="post-image" role="img" aria-label="Photo of a live event crowd behind the post title" style="background:linear-gradient(135deg,#4a4f58,#1e2228)"><span>Use mobile bidding at your live event to increase revenue</span></div>
      <p>Follow this Step-by-Step guide to learn how to easily create and manage your first auction.</p>
      <span class="btn btn-orange" style="left:56px;top:209px;width:88px;height:24px">Learn More</span>
    </article>

    <div class="company">
      <h2 class="h-display center">You're in Good Company</h2>
      <p class="company-sub center">Here are some other organizations that have run auctions with us:</p>
    </div>
    <span class="partner" style="left:163px"><i></i></span>
    <span class="partner" style="left:293px"><i></i></span>
    <span class="partner" style="left:424px"><i></i></span>
    <span class="partner" style="left:555px"><i></i></span>
  </section>

  <footer class="panel footer">
    <span class="footer-rule" style="left:283px"></span>
    <span class="footer-rule" style="left:548px"></span>
    <h4 style="left:98px;top:64px">QUICK LINKS</h4>
    <ul class="footer-links" style="left:98px;top:80px">
      <li>Home</li><li>How It Works</li><li>Pricing</li><li>About</li><li>Blog</li>
    </ul>
    <ul class="footer-links" style="left:185px;top:80px">
      <li>Silent Auctions</li><li>Browse Auctions</li>
    </ul>
    <div class="brand" style="left:330px;top:82px;font-size:17px;color:var(--blue)"><span class="brand-dot" style="width:14px;height:14px"></span>GivingGavelHub</div>
    <span class="social" style="left:377px"></span>
    <span class="social" style="left:405px"></span>
    <span class="social" style="left:434px"></span>
    <h4 style="left:588px;top:64px">OUR NEWSLETTER</h4>
    <p class="abs" style="left:588px;top:82px;font-size:7.5px;color:#d7e1ef">Your email</p>
    <span class="abs" style="left:588px;top:103px;width:147px;height:1px;background:rgba(255,255,255,.3)"></span>
    <span class="btn btn-orange" style="left:588px;top:117px;width:112px;height:25px;border-radius:13px">Subscribe Now</span>
    <p class="copyright">© 2023 GIVINGGAVELHUB LLC - ALL RIGHTS RESERVED</p>
  </footer>
</main>

</div>
</body>
</html>
```